Marwick Law Letterhead

We need a new letterhead design for a Law Firm. The address for the law firm is 1475 Calloway Street, Suite 210, Houston, Texas 77041. Phone Number: 832-361-9027; Fax Number: 832-614-7359. The logo is uploaded to the project.

```html
<!DOCTYPE html>
<html lang="en">
<head>
<meta charset="utf-8">
<title>Marwick Law Letterhead</title>
<link href="https://fonts.googleapis.com/css2?family=Montserrat:wght@400;500;600&display=swap" rel="stylesheet">
<style>
  :root {
    --navy: #1c3466;
    --red: #d0161f;
    --red-deep: #7d0a14;
    --ink: #232323;
    --paper: #ffffff;
    --backdrop: #e8e8ea;
  }
  * { box-sizing: border-box; margin: 0; padding: 0; }
  html, body {
    width: 1200px; height: 960px; overflow: hidden;
    background: var(--backdrop);
    font-family: "Montserrat", sans-serif;
    color: var(--ink);
  }
  .letterhead {
    position: absolute; left: 275px; top: 20px;
    width: 650px; height: 920px;
    background: var(--paper);
    box-shadow: 0 4px 18px rgba(0,0,0,0.12);
    overflow: hidden;
  }
  .brand {
    position: absolute; left: 36px; top: 44px;
    display: flex; align-items: center; gap: 10px;
  }
  .brand-mark {
    width: 30px; height: 30px; border-radius: 50%;
    background: var(--navy);
  }
  .brand-name {
    font-size: 24px; font-weight: 600; letter-spacing: 0.5px;
    color: var(--navy);
  }
  .contact-divider {
    position: absolute; left: 496px; top: 34px;
    width: 1px; height: 72px; background: var(--red);
  }
  .contact {
    position: absolute; left: 512px; top: 40px;
    font-size: 9.5px; line-height: 13px; color: var(--ink);
  }
  .contact-line { display: flex; align-items: center; gap: 6px; }
  .contact-line svg { width: 9px; height: 9px; fill: var(--red); }
  .contact address { font-style: normal; margin-bottom: 3px; }
  .header-rule {
    position: absolute; left: 26px; top: 146px;
    width: 600px; height: 1.5px; background: var(--red);
  }
  .recipient {
    position: absolute; left: 30px; top: 186px;
    font-size: 10px; line-height: 14px;
  }
  .letter-body {
    position: absolute; left: 30px; top: 258px; width: 570px;
    font-size: 9.5px; line-height: 13.8px; letter-spacing: 0.1px;
  }
  .letter-body p { margin-bottom: 16px; }
  .sign-off {
    position: absolute; left: 40px; top: 680px;
    font-size: 11px; font-weight: 500;
  }
  .signature {
    position: absolute; left: 56px; top: 700px;
    width: 90px; height: 28px; border-radius: 4px;
    background: linear-gradient(90deg, #ececec, #f6f6f6);
  }
  .footer-band {
    position: absolute; left: 0; bottom: 0;
    width: 650px; height: 150px;
    background: linear-gradient(180deg, var(--navy) 0%, var(--red) 55%, var(--red-deep) 100%);
  }
</style>
</head>
<body>
  <main class="letterhead">
    <div class="brand">
      <span class="brand-mark"></span>
      <span class="brand-name">Marwick Law</span>
    </div>

    <span class="contact-divider"></span>
    <div class="contact">
      <address>1475 Calloway Street,<br>Suite 210, Houston,<br>Texas 77041</address>
      <div class="contact-line">
        <svg viewBox="0 0 24 24"><path d="M6.6 10.8a15 15 0 0 0 6.6 6.6l2.2-2.2a1 1 0 0 1 1-.25 11.4 11.4 0 0 0 3.6.57 1 1 0 0 1 1 1V20a1 1 0 0 1-1 1A17 17 0 0 1 3 4a1 1 0 0 1 1-1h3.5a1 1 0 0 1 1 1c0 1.25.2 2.45.57 3.57a1 1 0 0 1-.25 1z"/></svg>
        <span>832-361-9027</span>
      </div>
      <div class="contact-line">
        <svg viewBox="0 0 24 24"><path d="M6 3h10v5H6zM4 9h16a2 2 0 0 1 2 2v7h-4v3H6v-3H2v-7a2 2 0 0 1 2-2zm4 8v2h8v-2z"/></svg>
        <span>832-614-7359</span>
      </div>
    </div>

    <span class="header-rule"></span>

    <div class="recipient">
      Mr/s<br>First Name and Last Name<br>Company Name<br>Address
    </div>

    <section class="letter-body">
      <p>Lorem ipsum dolor sit amet,consectetur adipiscing sed do eiusmod tempor incididunt laboreet dolore magna aliqua.Ut enim ad minim.veniam, quis nostrud exercitation ullamco laboris nisi ut aliquip exea commodo consequat.Lorem ipsum dolor sit amet,consectetur adipiscing sed do eiusmod tempor incididunt.labore et dolore magna aliqua. Ut enim</p>
      <p>Lorem ipsum dolor sit amet, consectetur adipiscing sed do eiusmod tempor incididunt labore et dolore magna aliqua. Ut enim ad minim veniam, quis nostrud exercitation ullamco laboris nisi ut aliquip exea commodo consequat.Duis aute irure dolor in reprehenderit in voluptate velit esse cillum irure dolor in reprehenderit in voluptate velit esse irure</p>
      <p>Lorem ipsum dolor sit amet, consectetur adipiscing sed do eiusmod tempor incididunt labore et dolore magna aliqua. consequat. Duis aute irure dolor in.reprehenderit in voluptate velit esse cillum dolore eu fugiat nulla pariatur. Excepteur sint occaecat cupidatat non proident, sunt in culpa qui officia deserunt mollit,</p>
      <p>Lorem ipsum dolor sit amet, consectetur adipiscing sed do eiusmod tempor incididunt labore et dolore magna aliqua. Ut enim Lorem ipsum dolor sit amet, consectetur adipiscing sed do eiusmod tempor incididunt labore et dolore magna aliqua. Ut enim Lorem ipsum aliqua.ipsum</p>
      <p>Lorem ipsum dolor sit amet, consectetur adipiscing sed do eiusmod tempor incididunt labore et dolore magna aliqua. Ut enim ad minim veniam, quis nostrud exercitation ullamco laboris nisi ut aliquip exea commodo consequat.Duis aute irure dolor in reprehenderit in voluptate velit esse cillum irure dolor in reprehenderit in voluptate velit esse irure</p>
      <p>Lorem ipsum dolor sit amet, consectetur adipiscing sed do eiusmod tempor incididunt labore et dolore magna aliqua. Ut enim ad minim veniam, quis nostrud exercitation ullamco laboris nisi ut aliquip exea commodo consequat.Duis aute irure dolor in reprehenderit in voluptate velit esse cillum irure dolor in reprehenderit in voluptate velit esse irure</p>
    </section>

    <p class="sign-off">Regards</p>
    <div class="signature" role="img" aria-label="Handwritten signature of Ellery"></div>

    <div class="footer-band" role="img" aria-label="Decorative navy and red footer artwork"></div>
  </main>
</body>
</html>
```